Website Design Project for Beauty & Wellness Professionals

As background information, I have a website that is focused on Beauty & Wellness Professionals:
- Job Search (www.lumarinovo.com)
- Business Classifieds (negocios.lumarinovo.com)
- Freelancer Classifieds (freelancer.lumarinovo.com)
- Course Reviews (cursos.lumarinovo.com)

All those websites use standard templates.

I need a DESIGN for the HOME PAGE (no coding) of the Website Platform that consolidates the four platforms under the same design.

Website designs that we like:
- quelvox.com
- brintmoor.com

Target Market(s)

Brazilian Professionals from Beauty & Wellness sector

Industry/Entity Type

Business

Requirements
Must have
• Website designs that we like:
- quelvox.com
- brintmoor.com

```html
<!DOCTYPE html>
<html lang="pt-BR">
<head>
<meta charset="utf-8">
<title>Lumarinovo – Beauty &amp; Wellness Careers</title>
<link href="https://fonts.googleapis.com/css2?family=Open+Sans:wght@400;600;700&display=swap" rel="stylesheet">
<style>
:root{
  --teal:#1b96c4;
  --teal-dark:#137aa2;
  --red:#d8262c;
  --pink:#e2456f;
  --ink:#333;
  --muted:#777;
  --line:#dcdcdc;
  --panel:#f2f2f2;
  --hero-a:#8f9aa4;
  --hero-b:#d9dde0;
}
*{box-sizing:border-box;margin:0;padding:0}
html,body{width:820px;height:1200px;overflow:hidden;background:#fff}
body{font-family:"Open Sans",Arial,sans-serif;color:var(--ink);font-size:11px;position:relative}
a{color:inherit;text-decoration:none}

/* header */
.site-header{height:60px;display:flex;justify-content:space-between;align-items:center;padding:0 60px}
.brand{display:flex;align-items:center;gap:8px;font-size:22px;font-weight:700;color:var(--teal)}
.brand-dot{width:22px;height:22px;border-radius:50%;background:var(--pink)}
.header-tools{text-align:right}
.header-tools .advertise{font-size:10px;color:var(--muted);margin-bottom:4px}
.header-tools .row{display:flex;align-items:center;gap:6px;justify-content:flex-end}
.phone{font-size:12px;color:var(--ink);display:flex;align-items:center;gap:4px;margin-right:6px}
.btn-small{background:var(--pink);color:#fff;font-size:10px;padding:3px 9px;border-radius:2px}

/* nav */
.main-nav{height:34px;background:var(--teal);display:flex;align-items:center;padding:0 60px;gap:2px}
.main-nav a{color:#fff;font-size:11px;font-weight:600;padding:9px 12px}
.main-nav a.active{background:var(--teal-dark)}

/* hero */
.hero{position:relative;height:290px;background:linear-gradient(120deg,var(--hero-a),var(--hero-b) 55%,#eef0f1)}
.hero-tagline{position:absolute;right:90px;top:150px;font-size:28px;font-style:italic;color:#3a4a55;font-weight:600}
.hero-arrow{position:absolute;top:120px;width:26px;height:40px;background:rgba(0,0,0,.35);display:flex;align-items:center;justify-content:center}
.hero-arrow.left{left:0}.hero-arrow.right{right:0}
.search-bar{position:absolute;left:60px;right:60px;bottom:36px;background:rgba(255,255,255,.55);padding:6px;display:flex;gap:6px}
.search-bar .field{background:#fff;border:1px solid #bbb;height:24px;font-size:10px;color:#666;display:flex;align-items:center;padding:0 8px}
.field.select{width:90px;justify-content:space-between}
.field.keywords{flex:1.3}
.field.location{flex:1}
.search-btn{background:var(--red);color:#fff;font-weight:700;font-size:11px;width:80px;display:flex;align-items:center;justify-content:center}

/* content */
.content{display:flex;gap:20px;padding:16px 60px 0;height:656px}
.primary{width:480px}
.secondary{width:200px}

.tabs{display:flex;border-bottom:2px solid var(--teal);height:26px}
.tab{font-size:10px;padding:6px 12px;background:var(--panel);border:1px solid var(--line);border-bottom:none;margin-right:3px;color:var(--muted)}
.tab.current{background:#fff;color:var(--teal);font-weight:600}

.job-list{list-style:none;margin-top:8px}
.job{display:grid;grid-template-columns:46px 1fr 150px 70px;gap:10px;padding:6px 0;border-bottom:1px solid #eee;min-height:58px;align-items:start}
.job-thumb{width:46px;height:34px;background:linear-gradient(135deg,#c9a7a0,#e9dad5)}
.job-title{color:var(--red);font-weight:600;font-size:10.5px;line-height:1.2}
.job-meta{font-size:8.5px;color:var(--muted);line-height:1.3;margin-top:2px}
.job-place{font-size:9.5px;line-height:1.3}
.job-date{font-size:9.5px;color:var(--red);line-height:1.3}
.see-more{text-align:right;font-size:9px;color:var(--teal);margin-top:6px}

.section-title{font-size:12px;font-weight:600;margin:22px 0 8px}
.courses{display:flex;gap:14px}
.course{flex:1}
.course-img{height:78px}
.course-img.one{background:linear-gradient(135deg,#b58f8a,#e5cfc9)}
.course-img.two{background:linear-gradient(135deg,#9a7f9a,#ddc9d8)}
.course-img.three{background:linear-gradient(135deg,#8ea5b3,#d6e0e6)}
.course p{font-size:9px;color:var(--muted);line-height:1.35;margin:6px 0}
.btn-read{display:inline-block;background:var(--red);color:#fff;font-size:9px;padding:3px 9px}

.welcome{background:var(--panel);border:1px solid var(--line);padding:16px 18px;margin-top:24px;height:196px}
.welcome h2{font-size:13px;font-weight:600;margin-bottom:10px}
.welcome p{font-size:9.5px;line-height:1.55;color:#555;margin-bottom:10px}

/* sidebar */
.ad-box{height:118px;background:linear-gradient(135deg,#2b2b2b,#8a1d22 60%,#e23a3a)}
.widget{margin-top:14px}
.widget h3{font-size:11.5px;font-weight:600;margin-bottom:5px}
.widget ul{list-style:none}
.widget li{font-size:9.5px;color:var(--teal);line-height:1.6}
.social{display:flex;gap:8px}
.social-item{text-align:center;font-size:7.5px;color:var(--muted);width:42px}
.social-item span{display:block;width:24px;height:24px;border-radius:50%;margin:0 auto 3px}
.s1{background:#3b5a98}.s2{background:#2fa9e0}.s3{background:#d34836}.s4{background:#f08a24}
.mobile-ad{margin-top:14px;height:140px;background:#4a4a4a;color:#fff;padding:12px;position:relative}
.mobile-ad small{font-size:9px;opacity:.8}
.mobile-ad strong{display:block;font-size:15px;line-height:1.15;margin-top:4px;width:100px}
.mobile-ad .phone-shot{position:absolute;right:12px;top:14px;width:56px;height:110px;border-radius:6px;background:linear-gradient(#7fc37a,#3a8f3f)}

/* bottom */
.wide-ad{margin:14px 60px 0;height:66px;background:linear-gradient(90deg,#2b2b2b,#8a1d22 60%,#e23a3a)}
.site-footer{text-align:center;margin-top:16px}
.footer-nav{font-size:9.5px;color:var(--muted)}
.footer-nav a{padding:0 6px}
.copyright{font-size:8.5px;color:#999;margin-top:6px}
</style>
</head>
<body>

<header class="site-header">
  <a class="brand" href="#"><span class="brand-dot"></span>Lumarinovo</a>
  <div class="header-tools">
    <div class="advertise">Advertise Job Vacancy</div>
    <div class="row">
      <span class="phone">
        <svg width="10" height="10" viewBox="0 0 10 10"><path d="M2 1l2 2-1 1.2c.6 1.2 1.6 2.2 2.8 2.8L7 6l2 2-1.3 1.5C4 9 1 6 .5 2.3z" fill="#1b96c4"/></svg>
        011.555.0192
      </span>
      <a class="btn-small" href="#">Login</a>
      <a class="btn-small" href="#">Register</a>
    </div>
  </div>
</header>

<nav class="main-nav">
  <a class="active" href="#">Home</a>
  <a href="#">Blog</a>
  <a href="#">For Professional</a>
  <a href="#">For Business</a>
  <a href="#">Events &amp; Partners</a>
  <a href="#">About Us</a>
  <a href="#">Contact Us</a>
</nav>

<section class="hero" role="img" aria-label="Bright modern office with a meeting table and large windows">
  <div class="hero-arrow left"><svg width="10" height="14" viewBox="0 0 10 14"><path d="M8 1L2 7l6 6" stroke="#fff" stroke-width="2" fill="none"/></svg></div>
  <div class="hero-arrow right"><svg width="10" height="14" viewBox="0 0 10 14"><path d="M2 1l6 6-6 6" stroke="#fff" stroke-width="2" fill="none"/></svg></div>
  <div class="hero-tagline">solutions simplified</div>
  <form class="search-bar">
    <div class="field select">Jobs <svg width="8" height="5" viewBox="0 0 8 5"><path d="M0 0h8L4 5z" fill="#666"/></svg></div>
    <div class="field keywords">Job Title, Keywords, Company</div>
    <div class="field location">Location</div>
    <div class="search-btn">SEARCH</div>
  </form>
</section>

<main class="content">
  <div class="primary">
    <div class="tabs">
      <span class="tab current">Featured Job Vacancies</span>
      <span class="tab">Latest Job Vacancies</span>
      <span class="tab">Job Vacancies</span>
    </div>
    <ul class="job-list">
      <li class="job">
        <div class="job-thumb"></div>
        <div><div class="job-title">Manicure – Jabaquara – São Paulo (SP)</div><div class="job-meta">Salão Aurivel – Unid. Jabaquara<br>Posted by Ana Souza</div></div>
        <div class="job-place">São Paulo – São Paulo, Brazil</div>
        <div class="job-date">July 25<br>2015</div>
      </li>
      <li class="job">
        <div class="job-thumb"></div>
        <div><div class="job-title">Assistant Hair Stylist – Moema – São Paulo (SP)</div><div class="job-meta">Salão Aurivel – Unid. Moema<br>Posted by Ana Souza</div></div>
        <div class="job-place">São Paulo – São Paulo, Brazil</div>
        <div class="job-date">July 25<br>2015</div>
      </li>
      <li class="job">
        <div class="job-thumb"></div>
        <div><div class="job-title">Manicure – Next to Vila Mariana – Sundays – SP</div><div class="job-meta">Studio Bela Vista – Unid. Centro<br>Posted by Ana Souza</div></div>
        <div class="job-place">São Paulo – São Paulo, Brazil</div>
        <div class="job-date">July 25<br>2015</div>
      </li>
    </ul>
    <div class="see-more">See More Featured Job Vacancies</div>

    <h2 class="section-title">Online Courses Cursivo</h2>
    <div class="courses">
      <article class="course">
        <div class="course-img one" role="img" aria-label="Beauty course lesson scene"></div>
        <p>Lorem ipsum is simply dummy text of the printing and typesetting.</p>
        <a class="btn-read" href="#">Read more</a>
      </article>
      <article class="course">
        <div class="course-img two" role="img" aria-label="Makeup course lesson scene"></div>
        <p>Lorem ipsum is simply dummy text of the printing and typesetting.</p>
        <a class="btn-read" href="#">Read more</a>
      </article>
      <article class="course">
        <div class="course-img three" role="img" aria-label="Wellness course lesson scene"></div>
        <p>Lorem ipsum is simply dummy text of the printing and typesetting.</p>
        <a class="btn-read" href="#">Read more</a>
      </article>
    </div>

    <section class="welcome">
      <h2>Welcome to Our Site</h2>
      <p>Lumarinovo was launched in early 2013 with the objective of strengthening the relationship between professionals and companies in the areas of Health, Beauty and Wellness, leveraging the development of professionals and entrepreneurs of this market.</p>
      <p>Due to requests from our corporate clients, we also make Special Projects for Companies. If interested, please contact us via our Contact Us.</p>
      <a class="btn-read" href="#">Read more</a>
    </section>
  </div>

  <aside class="secondary">
    <div class="ad-box" role="img" aria-label="Sports shoe sale advertisement"></div>
    <div class="widget">
      <h3>Search By</h3>
      <ul><li>Job Type List</li><li>Salary List</li><li>Job Category</li><li>Published Date</li><li>Keyword</li></ul>
    </div>
    <div class="widget">
      <h3>Job Vacancies</h3>
      <ul><li>Assistant Hairdresser</li><li>Assistant Cleaning</li><li>Hairdresser</li><li>Manicurist</li><li>Stylists</li><li>Eyebrow Designer</li><li>Podiatrist</li><li>More</li></ul>
    </div>
    <div class="widget">
      <h3>Follow Us</h3>
      <div class="social">
        <div class="social-item"><span class="s1"></span>Friendnet</div>
        <div class="social-item"><span class="s2"></span>Chirpline</div>
        <div class="social-item"><span class="s3"></span>Circlespace</div>
        <div class="social-item"><span class="s4"></span>RSS Feeds</div>
      </div>
    </div>
    <div class="mobile-ad">
      <small>Mobile Website</small>
      <strong>Search for jobs on the go</strong>
      <div class="phone-shot" role="img" aria-label="Smartphone showing the mobile job search"></div>
    </div>
  </aside>
</main>

<div class="wide-ad" role="img" aria-label="Wide sports shoe sale advertisement banner"></div>

<footer class="site-footer">
  <nav class="footer-nav">
    <a href="#">Home</a>|<a href="#">Blog</a>|<a href="#">For Professionals</a>|<a href="#">For Business</a>|<a href="#">Events &amp; Partners</a>|<a href="#">About Us</a>|<a href="#">Contact Us</a>
  </nav>
  <div class="copyright">Copyright © 2015 All Rights Reserved</div>
</footer>

</body>
</html>
```